Stationery Design Project

I need a stationary design for our company. we are based in Houston, TX and we are called Mira Vell Lending. And we are wanting to brand our MoneyMendPlus program, which includes our tax preparation and restoration, credit repair service. Although our business offers other programs, we are interested in mainly focusing on The MoneyMendPlus program. We are looking for way to brand our ourselves and I believe that a great stationery design will help in achieving this goal. Our logo design is blue and light blue. the slogan is orange.

Industry/Entity Type

Business

Requirements
Must have
• Address: 30871 Calloway Ln. B-22
Houston, TX 75419
Tel. 555-318-6207
Fax 555-294-7153
www.miravelllending.example
info@miravelllending.example
Our Slogan: Happiness, Restored!

```html
<!DOCTYPE html>
<html lang="en">
<head>
<meta charset="utf-8">
<title>MoneyMendPlus Business Cards</title>
<link rel="stylesheet" href="https://fonts.googleapis.com/css2?family=Open+Sans:wght@400;600&family=Cinzel:wght@400&display=swap">
<style>
  :root {
    --backdrop: #efece6;
    --card-white: #ffffff;
    --card-pale: #cfe3f4;
    --navy: #0f3a63;
    --brand-blue: #1a6aa8;
    --gradient-start: #0a97d8;
    --gradient-end: #1c3e8e;
    --slogan-orange: #ec7a22;
    --text-dark: #2b2b2b;
    --text-grey: #4a4a4a;
    --frame-light: #e9eef3;
  }
  * { margin: 0; padding: 0; box-sizing: border-box; }
  html, body { width: 1200px; height: 772px; overflow: hidden; }
  body {
    background: var(--backdrop);
    position: relative;
    font-family: "Open Sans", Arial, sans-serif;
  }
  .card {
    position: absolute;
    border-radius: 20px;
    box-shadow: 2px 3px 6px rgba(0,0,0,0.25);
    overflow: hidden;
  }
  .card--front-detail { left: 87px; top: 85px; width: 509px; height: 290px; background: var(--card-white); }
  .card--back-gradient { left: 628px; top: 78px; width: 511px; height: 290px; background: linear-gradient(90deg, var(--gradient-start), var(--gradient-end)); }
  .card--back-pale { left: 84px; top: 403px; width: 508px; height: 289px; background: var(--card-pale); }
  .card--back-white { left: 633px; top: 403px; width: 508px; height: 289px; background: var(--card-white); }

  .program-name {
    position: absolute;
    font-weight: 600;
    color: var(--brand-blue);
    white-space: nowrap;
    letter-spacing: -0.5px;
  }
  .card--front-detail .program-name { left: 27px; top: 88px; font-size: 38px; }
  .card--back-white .program-name { left: 0; width: 100%; text-align: center; top: 168px; font-size: 42px; }

  .contact {
    position: absolute;
    left: 29px;
    font-size: 12.5px;
    color: var(--text-dark);
    line-height: 17px;
  }
  .contact--address { top: 162px; }
  .contact--lines { top: 212px; }
  .contact--web { top: 251px; }
  .contact .label { color: var(--slogan-orange); }

  .company-square {
    position: absolute;
    background: var(--navy);
    display: flex;
    align-items: center;
    justify-content: center;
    text-align: center;
    color: #ffffff;
    font-family: "Open Sans", Arial, sans-serif;
    font-weight: 400;
  }
  .company-square--small {
    left: 358px; top: 117px; width: 82px; height: 82px;
    font-size: 9px; padding: 4px;
    box-shadow: 0 0 0 3px var(--frame-light), 1px 2px 4px rgba(0,0,0,0.3);
  }
  .company-square--large {
    width: 150px; height: 150px; font-size: 14px; padding: 10px;
    border: 4px solid var(--frame-light);
  }
  .card--back-gradient .company-square--large { left: 180px; top: 52px; box-shadow: 1px 2px 5px rgba(0,0,0,0.3); }
  .card--back-pale .company-square--large { left: 178px; top: 50px; border-color: #dfeaf3; box-shadow: 0 0 0 1px #8a9bab; }

  .slogan {
    position: absolute;
    left: 320px; top: 218px; width: 160px;
    text-align: center;
    font-family: "Cinzel", "Times New Roman", serif;
    font-size: 20px;
    line-height: 25px;
    color: var(--text-grey);
    letter-spacing: 0.5px;
  }

  .web-address {
    position: absolute;
    left: 0; width: 100%;
    text-align: center;
    font-size: 12px;
    letter-spacing: 5.2px;
  }
  .card--back-gradient .web-address { top: 240px; color: #d7e6f5; }
  .card--back-pale .web-address { top: 240px; color: var(--navy); }
  .card--back-white .web-address { top: 240px; color: var(--navy); }
</style>
</head>
<body>

  <section class="card card--front-detail" aria-label="Card front with contact details">
    <div class="program-name">MoneyMendPlus</div>
    <p class="contact contact--address">30871 Calloway Ln. B-22, Houston, TX 75419</p>
    <p class="contact contact--lines">
      <span class="label">T:</span> 555-318-6207, <span class="label">F:</span> 555-294-7153<br>
      <span class="label">E:</span> info@miravelllending.example
    </p>
    <p class="contact contact--web">www.miravelllending.example</p>
    <div class="company-square company-square--small">Mira Vell Lending</div>
    <p class="slogan">HAPPINESS, RESTORED!</p>
  </section>

  <section class="card card--back-gradient" aria-label="Card back, blue gradient">
    <div class="company-square company-square--large">Mira Vell Lending</div>
    <p class="web-address">www.miravelllending.example</p>
  </section>

  <section class="card card--back-pale" aria-label="Card back, pale blue">
    <div class="company-square company-square--large">Mira Vell Lending</div>
    <p class="web-address">www.miravelllending.example</p>
  </section>

  <section class="card card--back-white" aria-label="Card back, white">
    <div class="program-name">MoneyMendPlus</div>
    <p class="web-address">www.miravelllending.example</p>
  </section>

</body>
</html>
```